Business Card Design Project

Business card based on attached logo

Todd Merrick
Todd@lorvantest.com
877-514-9073 ext. 318
Www.LorvanTest.com

Industry/Entity Type

Business

```html
<!DOCTYPE html>
<html lang="en">
<head>
<meta charset="utf-8">
<title>Lorvan Test — Business Card Set</title>
<link href="https://fonts.googleapis.com/css2?family=Archivo:wght@800&family=Roboto:wght@400&display=swap" rel="stylesheet">
<style>
  :root {
    --stage: #8b8d90;
    --paper: #ffffff;
    --ink: #231f20;
    --red: #e3262b;
    --red-deep: #c0202a;
    --charcoal: #1c1c1c;
    --charcoal-light: #3a3a3a;
    --white: #ffffff;
  }
  * { box-sizing: border-box; margin: 0; padding: 0; }
  html, body { width: 1200px; height: 720px; overflow: hidden; background: var(--stage); }
  .sheet { position: relative; width: 1200px; height: 720px; }
  .card {
    position: absolute; width: 563px; height: 322px; overflow: hidden;
    font-family: "Roboto", Arial, sans-serif;
  }
  .card--front { left: 28px; top: 26px; background: var(--paper); }
  .card--red { left: 612px; top: 26px; background: linear-gradient(120deg, var(--red) 0%, var(--red-deep) 100%); }
  .card--light { left: 28px; top: 373px; background: var(--paper); }
  .card--dark { left: 612px; top: 373px; background: radial-gradient(ellipse at 50% 40%, var(--charcoal-light) 0%, var(--charcoal) 75%); }

  .wordmark {
    position: absolute; display: flex; align-items: center; gap: 12px;
    font-family: "Archivo", "Arial Black", sans-serif; font-weight: 800;
    font-size: 54px; line-height: 1; letter-spacing: -1px; color: var(--ink);
  }
  .wordmark__square { width: 22px; height: 22px; background: var(--red); flex: none; }
  .wordmark--on-color { color: var(--white); }
  .wordmark--on-color .wordmark__square { background: var(--white); }
  .card--front .wordmark { left: 50px; top: 72px; }
  .card--red .wordmark { left: 34px; top: 60px; font-size: 60px; }
  .card--light .wordmark, .card--dark .wordmark { left: 0; right: 0; top: 120px; justify-content: center; font-size: 60px; }

  .holder-name {
    position: absolute; left: 60px; top: 224px;
    font-size: 19px; color: var(--red); letter-spacing: 0.3px;
  }
  .swoosh { position: absolute; inset: 0; }
  .contact {
    position: absolute; right: 10px; top: 244px; list-style: none;
    color: var(--white); font-size: 15.5px; text-align: right;
  }
  .contact li { display: flex; align-items: center; justify-content: flex-end; gap: 7px; height: 26px; }
  .contact svg { width: 12px; height: 12px; }

  .site {
    position: absolute; font-size: 17px; letter-spacing: 3px;
  }
  .card--red .site { left: 36px; bottom: 14px; color: var(--white); }
  .card--light .site { left: 0; right: 0; bottom: 24px; text-align: center; color: var(--ink); }
  .card--dark .site { left: 0; right: 0; bottom: 24px; text-align: center; color: var(--white); }

  .faint-block {
    position: absolute; right: 20px; bottom: 70px; width: 110px; height: 110px;
    background: rgba(255,255,255,0.14);
  }
</style>
</head>
<body>
<main class="sheet">

  <section class="card card--front" aria-label="Business card front">
    <svg class="swoosh" viewBox="0 0 563 322" preserveAspectRatio="none" aria-hidden="true">
      <defs>
        <linearGradient id="dark-band" x1="0" y1="0" x2="1" y2="0">
          <stop offset="0" stop-color="#151515"/><stop offset="1" stop-color="#3a3a3a"/>
        </linearGradient>
      </defs>
      <path d="M0,322 L0,290 C170,330 360,250 563,140 L563,322 Z" fill="url(#dark-band)"/>
      <path d="M0,268 C150,330 360,270 563,140 L563,150 C360,282 150,332 0,300 Z" fill="#ffffff"/>
      <path d="M0,250 C140,300 340,250 563,134 L563,146 C340,265 140,320 0,282 Z" fill="var(--red)"/>
      <path d="M50,270 C200,300 360,250 520,170 C360,262 200,292 50,270 Z" fill="var(--red-deep)"/>
    </svg>
    <div class="wordmark"><span>LORVAN TEST</span><span class="wordmark__square"></span></div>
    <p class="holder-name">TODD MERRICK</p>
    <ul class="contact">
      <li><svg viewBox="0 0 12 12"><path d="M3 1 L5 3.5 L4 5 C4.8 6.6 5.6 7.4 7 8 L8.5 7 L11 9 L9.5 11 C5 10.5 1.5 7 1 2.5 Z" fill="#fff"/></svg>877-514-9073 ext. 318</li>
      <li><svg viewBox="0 0 12 12"><rect x="0.5" y="2.5" width="11" height="7.5" fill="#fff"/><path d="M0.5 2.5 L6 7 L11.5 2.5" stroke="#222" fill="none"/></svg>Todd@lorvantest.com</li>
      <li><svg viewBox="0 0 12 12"><circle cx="6" cy="6" r="5" stroke="#fff" fill="none"/><ellipse cx="6" cy="6" rx="2.2" ry="5" stroke="#fff" fill="none"/><path d="M1 6 H11" stroke="#fff"/></svg>www.lorvantest.com</li>
    </ul>
  </section>

  <section class="card card--red" aria-label="Business card back, red">
    <div class="faint-block"></div>
    <div class="wordmark wordmark--on-color"><span>LORVAN TEST</span><span class="wordmark__square"></span></div>
    <p class="site">www.lorvantest.com</p>
  </section>

  <section class="card card--light" aria-label="Business card back, white">
    <div class="wordmark"><span>LORVAN TEST</span><span class="wordmark__square"></span></div>
    <p class="site">www.lorvantest.com</p>
  </section>

  <section class="card card--dark" aria-label="Business card back, dark">
    <div class="wordmark wordmark--on-color"><span>LORVAN TEST</span><span class="wordmark__square"></span></div>
    <p class="site">www.lorvantest.com</p>
  </section>

</main>
</body>
</html>
```